Need 3 posters for in-store display

Hi Marlene,

Hope you are well.
I need 3 posters for display in my restaurant.

Poster 1: To be print in A1 size vertical
Title: YUMBELLA COMBO $19.50
Choose any Pho OR Noodle Salads
Choose Spring Rolls (5 rolls) OR Ricepaper Rolls (2 rolls)
Choose any Cans OR Water

What I like to see:
- These poster will be place near my counter so I want it to grab customer attention.
- You must use photos to show products
- Make it easy to understand and for customer to follow

Poster 2: To be print in A4 size vertical
Title: ADD TO YOUR ORDER
SpringRolls (Crab / vegetarian) $6 / 5 rolls
Extra Meat $2
Extra Noodles $1
Extra Vegs $1.5
Extra Tofu $2
Extra Crackling $3

Poster 3: To be print in A1 size vertical
Title: FIESTO LOOMA PARTY
Catering Menu Options:
- PHO (Beef, Chicken, Vegan) $12.50 per bowl
- NOODLE SALADS (Beef, Chicken, BBQ Pork, Vegan) $12.50 per bowl
- SpringRolls (Crab / vegetarian) $12.50 for 10 rolls
- Ricepaper Rolls (Prawn, Beef, Chicken, BBQ Pork, Tofu) $12.5 / 5 rolls
- Fried Rice (Prawn, Tofu) $50 per tray (serve 5-6)

Terms & Conditions for All Catering Orders:
1) Minimum orders $200 (Pick-Up from shop Only)
2) All orders must be paid upfront
3) Requires $300 bond for Soup Tank
4) Please give us 48hours notice

• For the YUMBELLA COMBO
• it would be nice to have an image of the battle of water to visually complete the meal deal
• please see attachment of the Crestvale Peak Water

```html
<!DOCTYPE html>
<html lang="en">
<head>
<meta charset="utf-8">
<title>Yumbella Combo Poster</title>
<link rel="stylesheet" href="https://fonts.googleapis.com/css2?family=Open+Sans:wght@700;800&family=Jost:wght@400;500&display=swap">
<style>
  :root {
    --ink-dark: #151412;
    --title-green: #9fd11c;
    --white: #ffffff;
    --gold: #d4ad4a;
    --gold-light: #f3d98a;
    --gold-deep: #b8902e;
    --wood: #8a6a4c;
    --wood-dark: #4a382a;
    --footer-text: #2a2418;
  }
  * { margin: 0; padding: 0; box-sizing: border-box; }
  html, body { width: 872px; height: 1200px; overflow: hidden; background: var(--ink-dark); }
  .poster { position: relative; width: 872px; height: 1200px; overflow: hidden; }

  .backdrop-photo {
    position: absolute; inset: 0;
    background: linear-gradient(180deg, #3a3733 0%, #24221f 22%, #141311 50%, #2a231c 60%, var(--wood-dark) 70%, var(--wood) 86%, #7a5c40 100%);
  }
  .bowls-photo {
    position: absolute; left: 82px; top: 662px; width: 708px; height: 440px;
    border-radius: 10px;
    background: linear-gradient(180deg, #6e5640 0%, #8c6a4c 45%, #a08a74 75%, #b9b3aa 100%);
  }

  .title-main {
    position: absolute; left: 84px; top: 60px;
    font-family: "Open Sans", sans-serif; font-weight: 800;
    font-size: 100px; line-height: 100px; letter-spacing: -2px;
    color: var(--title-green);
  }
  .title-sub {
    position: absolute; left: 84px; top: 150px;
    font-family: "Open Sans", sans-serif; font-weight: 800;
    font-size: 76px; line-height: 76px; letter-spacing: -1px;
    color: var(--white);
  }
  .price-band {
    position: absolute; left: 386px; top: 162px; width: 385px; height: 60px;
    background: linear-gradient(90deg, rgba(184,144,46,0) 0%, var(--gold-deep) 10%, var(--gold-light) 55%, var(--gold) 100%);
  }
  .price {
    position: absolute; left: 430px; top: 152px;
    font-family: "Open Sans", sans-serif; font-weight: 800;
    font-size: 72px; line-height: 80px; color: var(--ink-dark);
  }

  .choice-frame { position: absolute; left: 96px; top: 282px; width: 682px; height: 336px; }
  .choice-heading {
    position: absolute; left: 336px; top: 270px; width: 200px;
    font-family: "Open Sans", sans-serif; font-weight: 700;
    font-size: 40px; line-height: 44px; text-align: center;
    color: var(--gold); letter-spacing: 1px;
  }
  .choice-divider {
    position: absolute; left: 412px; width: 2px;
    background: var(--title-green);
  }
  .choice-or {
    position: absolute; left: 383px; top: 440px; width: 60px;
    font-family: "Jost", sans-serif; font-weight: 500;
    font-size: 34px; line-height: 34px; text-align: center; color: var(--title-green);
  }
  .choice-item {
    position: absolute;
    font-family: "Jost", sans-serif; font-weight: 400;
    font-size: 34px; line-height: 36px; color: var(--white); white-space: nowrap;
  }
  .choice-item.left { right: 510px; text-align: right; }
  .choice-item.right { left: 462px; }
  .choice-note {
    position: absolute;
    font-family: "Jost", sans-serif; font-weight: 400;
    font-size: 23px; line-height: 26px; color: var(--white);
  }
  .choice-note.left { right: 510px; }
  .choice-note.right { left: 462px; }

  .footer-band {
    position: absolute; left: 0; top: 1134px; width: 872px; height: 66px;
    background: linear-gradient(90deg, var(--gold) 0%, var(--gold-light) 45%, #f6df97 70%, var(--gold) 100%);
  }
  .footer-phone {
    position: absolute; left: 46px; top: 1150px;
    font-family: "Jost", sans-serif; font-weight: 500;
    font-size: 24px; line-height: 32px; color: var(--footer-text);
  }
  .footer-web {
    position: absolute; left: 530px; top: 1150px; display: flex; align-items: center; gap: 12px;
    font-family: "Jost", sans-serif; font-weight: 500;
    font-size: 24px; line-height: 32px; color: var(--footer-text);
  }
  .footer-web svg { width: 28px; height: 28px; }
</style>
</head>
<body>
<div class="poster">
  <div class="backdrop-photo" role="img" aria-label="Blurred photo of ricepaper rolls and dipping sauce above a wooden table"></div>
  <div class="bowls-photo" role="img" aria-label="Photo of three white bowls of beef noodle salad with bean sprouts, herbs and crushed peanuts"></div>

  <div class="title-main">YUMBELLA</div>
  <div class="title-sub">COMBO</div>
  <div class="price-band"></div>
  <div class="price">$19.50</div>

  <svg class="choice-frame" viewBox="0 0 682 336" aria-hidden="true">
    <path d="M232 10 H20 Q2 10 2 28 V316 Q2 334 20 334 H662 Q680 334 680 316 V28 Q680 10 662 10 H450"
          fill="none" stroke="#d4ad4a" stroke-width="2"/>
  </svg>
  <div class="choice-heading">CHOOSE</div>
  <div class="choice-divider" style="top:340px;height:96px;"></div>
  <div class="choice-divider" style="top:482px;height:98px;"></div>
  <div class="choice-or">OR</div>

  <div class="choice-item left" style="top:352px;">ANY PHO</div>
  <div class="choice-item right" style="top:352px;">NOODLE SALADS</div>
  <div class="choice-item left" style="top:426px;">SPRING ROLLS</div>
  <div class="choice-item right" style="top:426px;">RICEPAPER ROLLS</div>
  <div class="choice-note left" style="top:470px;">(5 ROLLS)</div>
  <div class="choice-note right" style="top:470px;">(2 ROLLS)</div>
  <div class="choice-item left" style="top:538px;">ANY CANS</div>
  <div class="choice-item right" style="top:538px;">WATER</div>

  <div class="footer-band"></div>
  <div class="footer-phone">Call Us:0400 555 218</div>
  <div class="footer-web">
    <svg viewBox="0 0 28 28" aria-hidden="true">
      <circle cx="14" cy="14" r="12" fill="none" stroke="#2a2418" stroke-width="1.6"/>
      <circle cx="14" cy="14" r="8.5" fill="#2a2418"/>
      <ellipse cx="14" cy="14" rx="3.5" ry="8.5" fill="none" stroke="#f3d98a" stroke-width="1.2"/>
      <line x1="5.5" y1="14" x2="22.5" y2="14" stroke="#f3d98a" stroke-width="1.2"/>
      <line x1="7" y1="10" x2="21" y2="10" stroke="#f3d98a" stroke-width="1"/>
      <line x1="7" y1="18" x2="21" y2="18" stroke="#f3d98a" stroke-width="1"/>
    </svg>
    <span>www.yumbellaeats.com</span>
  </div>
</div>
</body>
</html>
```